Clear Harbor Business card

We are a company that owns 2 compliance software programs for TV, Radio and Cable industries as well as an online job board. We need a professional business card that incorproates all three logos.

```html
<!DOCTYPE html>
<html lang="en">
<head>
<meta charset="utf-8">
<title>Clear Harbor Business Card</title>
<link href="https://fonts.googleapis.com/css2?family=Roboto:wght@400;500;700&display=swap" rel="stylesheet">
<style>
  :root {
    --backdrop: #3a3b3e;
    --card: #ffffff;
    --card-shade: #ececed;
    --navy: #2a2566;
    --red: #e8321f;
    --blue: #1e8fd1;
    --ink: #2f2f3a;
    --rule: #5a5690;
  }
  * { margin: 0; padding: 0; box-sizing: border-box; }
  html, body { width: 1200px; height: 900px; overflow: hidden; }
  body {
    background: var(--backdrop);
    font-family: "Roboto", Arial, sans-serif;
    position: relative;
  }
  .business-card {
    position: absolute;
    left: 100px; top: 165px;
    width: 1000px; height: 570px;
    border-radius: 36px;
    overflow: hidden;
    background: radial-gradient(ellipse at 40% 30%, var(--card) 55%, var(--card-shade) 100%);
  }
  .card-swoosh { position: absolute; inset: 0; }
  .brand-row {
    position: absolute;
    left: 60px; top: 150px;
    display: flex; align-items: center;
  }
  .brand-name {
    font-size: 22px; font-weight: 700;
    color: var(--navy);
    padding: 0 22px;
    display: flex; align-items: center; gap: 8px;
  }
  .brand-name:first-child { padding-left: 0; }
  .brand-dot { width: 14px; height: 14px; border-radius: 50%; background: var(--blue); }
  .brand-divider { width: 1px; height: 56px; background: var(--rule); }
  .contact-divider {
    position: absolute; left: 560px; top: 190px;
    width: 1px; height: 240px; background: var(--rule);
  }
  .contact-block { position: absolute; left: 595px; top: 185px; color: var(--ink); }
  .person-name {
    font-size: 36px; font-weight: 700; letter-spacing: 2px;
    color: var(--navy); text-transform: uppercase;
  }
  .person-role { font-size: 24px; margin: 4px 0 18px; }
  .address { font-size: 22px; line-height: 1.35; margin-bottom: 10px; }
  .contact-line {
    font-size: 22px; line-height: 1.45;
    display: flex; align-items: center; gap: 12px;
  }
  .contact-line svg { width: 16px; height: 16px; flex: none; }
</style>
</head>
<body>
  <div class="business-card">
    <svg class="card-swoosh" viewBox="0 0 1000 570" preserveAspectRatio="none">
      <path d="M0,300 C220,420 560,515 860,570 L0,570 Z" fill="var(--navy)"/>
      <path d="M0,300 C220,420 560,515 860,570" fill="none" stroke="#ffffff" stroke-width="14"/>
      <path d="M120,352 C380,468 690,538 1000,556" fill="none" stroke="var(--red)" stroke-width="7"/>
    </svg>

    <div class="brand-row">
      <div class="brand-name">AirCheck Pro</div>
      <div class="brand-divider"></div>
      <div class="brand-name">WireCheck Pro</div>
      <div class="brand-divider"></div>
      <div class="brand-name"><span class="brand-dot"></span>CastJobs.net</div>
    </div>

    <div class="contact-divider"></div>

    <div class="contact-block">
      <h1 class="person-name">Daniel Reyes</h1>
      <p class="person-role">Director</p>
      <p class="address">48 Alder Lane,<br>Westbrook, NZ, 4120</p>
      <p class="contact-line">
        <svg viewBox="0 0 16 16"><path d="M4 1 L6.5 4 L5 6 C6 8.5 7.5 10 10 11 L12 9.5 L15 12 L13 15 C7 14.5 1.5 9 1 3 Z" fill="var(--navy)"/></svg>
        (555) 010-4821
      </p>
      <p class="contact-line">
        <svg viewBox="0 0 16 16"><rect x="1" y="3" width="14" height="10" rx="1.5" fill="none" stroke="var(--navy)" stroke-width="1.8"/><path d="M1.5 4 L8 9 L14.5 4" fill="none" stroke="var(--navy)" stroke-width="1.6"/></svg>
        info@ClearHarbor.com
      </p>
      <p class="contact-line">
        <svg viewBox="0 0 16 16"><circle cx="8" cy="8" r="6.5" fill="none" stroke="var(--navy)" stroke-width="1.6"/><ellipse cx="8" cy="8" rx="3" ry="6.5" fill="none" stroke="var(--navy)" stroke-width="1.3"/><path d="M1.5 8 H14.5" stroke="var(--navy)" stroke-width="1.3"/></svg>
        www.ClearHarbor.com
      </p>
    </div>
  </div>
</body>
</html>
```